SkyvornQ Business Cards and Stationary Design

Need a design for our business cards and stationary. I want to carry on the theme of the logo. I want the business cards to have a design on the back. I would like the business cards and the stationary to carry the same theme, design scheme, and branding

Target Market(s)

Airlines and Maintenance Facilities

Industry/Entity Type

Aviation

Contact Information for Business Card

Name
Position Title
Address: 4827 Trellis Hollow Road, Fort Pierce, Florida, 34951
Office Number
Mobile Number
Email
Website

Font styles to use
Serif
Sans Serif

Colors

Designer to choose colors to be used in the design.

```html
<!DOCTYPE html>
<html lang="en">
<head>
<meta charset="utf-8">
<title>SkyvornQ Business Card</title>
<link rel="stylesheet" href="https://fonts.googleapis.com/css2?family=Source+Sans+3:wght@400;600;700&display=swap">
<style>
  :root {
    --navy: #0d2a56;
    --navy-deep: #0a2249;
    --blue: #1a6fc0;
    --grey-text: #4a4f57;
    --paper: #ffffff;
    --backdrop: #e9ecf0;
  }
  * { margin: 0; padding: 0; box-sizing: border-box; }
  html, body { width: 1200px; height: 872px; overflow: hidden; }
  body {
    background: var(--backdrop);
    font-family: "Source Sans 3", sans-serif;
    display: flex;
    flex-direction: column;
    align-items: center;
    justify-content: center;
    gap: 40px;
  }
  .card {
    width: 660px;
    height: 377px;
    position: relative;
    box-shadow: 0 6px 20px rgba(10, 30, 60, 0.18);
    overflow: hidden;
  }
  /* Back of card */
  .card-back {
    background: radial-gradient(circle at 60% 40%, #123465 0%, var(--navy-deep) 75%);
    display: flex;
    flex-direction: column;
    align-items: center;
    justify-content: center;
    gap: 22px;
    color: var(--paper);
  }
  .brand {
    display: flex;
    align-items: center;
    gap: 18px;
  }
  .brand-dot {
    width: 52px; height: 52px;
    border-radius: 50%;
    border: 6px solid currentColor;
  }
  .brand-name {
    font-weight: 700;
    font-size: 50px;
    letter-spacing: 8px;
    text-transform: uppercase;
  }
  .back-url {
    font-size: 20px;
    letter-spacing: 4px;
  }
  /* Front of card */
  .card-front { background: var(--paper); }
  .front-brand {
    position: absolute;
    top: 62px;
    right: 44px;
    color: var(--navy);
  }
  .front-brand .brand-name { font-size: 40px; letter-spacing: 6px; }
  .front-brand .brand-dot { width: 42px; height: 42px; border-width: 5px; border-color: var(--blue); }
  .holder {
    position: absolute;
    top: 86px;
    left: 46px;
  }
  .holder-name {
    color: var(--navy);
    font-weight: 600;
    font-size: 26px;
    letter-spacing: 0.3px;
    text-transform: uppercase;
  }
  .holder-title {
    color: var(--grey-text);
    font-size: 21px;
    text-transform: uppercase;
    margin-top: 2px;
  }
  .contact {
    position: absolute;
    left: 46px;
    bottom: 38px;
    list-style: none;
    color: #2a2e35;
    font-size: 17px;
    line-height: 1;
  }
  .contact li {
    display: flex;
    align-items: center;
    gap: 8px;
    margin-top: 7px;
  }
  .contact li.address { margin-top: 18px; }
  .contact svg { width: 16px; height: 16px; flex: none; }
  .icon-ring { fill: none; stroke: var(--blue); stroke-width: 1.6; }
  .icon-mark { fill: var(--blue); }
  .icon-line { fill: none; stroke: var(--blue); stroke-width: 1.4; }
</style>
</head>
<body>

  <section class="card card-back" aria-label="Card back">
    <div class="brand">
      <span class="brand-dot"></span>
      <span class="brand-name">SkyvornQ</span>
    </div>
    <div class="back-url">www.skyvornq.com</div>
  </section>

  <section class="card card-front" aria-label="Card front">
    <div class="brand front-brand">
      <span class="brand-dot"></span>
      <span class="brand-name">SkyvornQ</span>
    </div>

    <div class="holder">
      <div class="holder-name">Darren Holloway</div>
      <div class="holder-title">President</div>
    </div>

    <ul class="contact">
      <li>
        <svg viewBox="0 0 16 16" aria-hidden="true"><circle class="icon-ring" cx="8" cy="8" r="7"/><path class="icon-mark" d="M5 4.2l1.6-.2.8 2-1 .8a6 6 0 0 0 2.8 2.8l.8-1 2 .8-.2 1.6c-3.6.4-7.2-3.2-6.8-6.8z"/></svg>
        012-555-0148
      </li>
      <li>
        <svg viewBox="0 0 16 16" aria-hidden="true"><circle class="icon-ring" cx="8" cy="8" r="7"/><rect class="icon-line" x="5.6" y="3.6" width="4.8" height="8.8" rx="0.8"/><circle class="icon-mark" cx="8" cy="11" r="0.6"/></svg>
        012-555-0176
      </li>
      <li>
        <svg viewBox="0 0 16 16" aria-hidden="true"><circle class="icon-ring" cx="8" cy="8" r="7"/><rect class="icon-line" x="4" y="5.2" width="8" height="5.6"/><path class="icon-line" d="M4 5.2l4 3 4-3"/></svg>
        info@skyvornq.com
      </li>
      <li>
        <svg viewBox="0 0 16 16" aria-hidden="true"><circle class="icon-ring" cx="8" cy="8" r="7"/><ellipse class="icon-line" cx="8" cy="8" rx="2.6" ry="6.4"/><path class="icon-line" d="M1.6 8h12.8M2.6 5h10.8M2.6 11h10.8"/></svg>
        www.skyvornq.com
      </li>
      <li class="address">
        <svg viewBox="0 0 16 16" aria-hidden="true"><circle class="icon-ring" cx="8" cy="8" r="7"/><path class="icon-mark" d="M8 3.4a3 3 0 0 1 3 3c0 2.2-3 5.8-3 5.8S5 8.6 5 6.4a3 3 0 0 1 3-3zm0 1.8a1.2 1.2 0 1 0 0 2.4 1.2 1.2 0 0 0 0-2.4z"/></svg>
        4827 Trellis Hollow Road, Fort Pierce, Florida, 34951
      </li>
    </ul>
  </section>

</body>
</html>
```